Business Card Design (NEW FILES)

ATTENTION: New vector files are available. Please update your design to reflect/use the new (better resolution) logo images.

Seeking a unique and professional business card design for a commercial drone photography/videography business. The layout should feature
the logo (attached) and include the following information:
Owen Tarrick
614-502-7738
www.skylarkreelworks.example
NRD Certified Remote Pilot

Owen Tarrick

```html
<!DOCTYPE html>
<html lang="en">
<head>
<meta charset="utf-8">
<title>Skylark Reelworks — Business Card</title>
<link rel="stylesheet" href="https://fonts.googleapis.com/css2?family=Open+Sans:wght@400;600;700&display=swap">
<style>
  :root {
    --stage: #222222;
    --navy: #161a4b;
    --navy-deep: #11143c;
    --pattern-blue: #2a3f9a;
    --orange: #ef8a3c;
    --white: #ffffff;
  }
  * { box-sizing: border-box; margin: 0; padding: 0; }
  html, body { width: 1200px; height: 780px; overflow: hidden; }
  body {
    background: var(--stage);
    font-family: "Open Sans", Arial, sans-serif;
    color: var(--white);
    display: flex;
    align-items: center;
    justify-content: center;
    gap: 40px;
  }
  .card {
    width: 540px;
    height: 310px;
    background: var(--navy);
    position: relative;
    overflow: hidden;
    box-shadow: 0 10px 30px rgba(0,0,0,.45);
  }

  /* Front */
  .brand-block {
    position: absolute;
    left: 0; top: 0;
    width: 270px; height: 310px;
    display: flex; flex-direction: column;
    align-items: center; justify-content: center;
  }
  .brand-name {
    display: flex; align-items: center; gap: 10px;
    font-size: 24px; font-weight: 600; color: var(--white);
    letter-spacing: .5px;
    margin-top: -30px;
  }
  .brand-dot {
    width: 14px; height: 14px; border-radius: 50%;
    background: var(--orange);
  }
  .credentials {
    position: absolute;
    left: 0; bottom: 48px; width: 270px;
    text-align: center;
    font-size: 14px; line-height: 1.45;
  }
  .divider {
    position: absolute;
    left: 270px; top: 70px;
    width: 1px; height: 170px;
    background: var(--orange);
  }
  .contact-block {
    position: absolute;
    left: 296px; top: 82px;
  }
  .person-name { font-size: 26px; font-weight: 700; line-height: 1.1; }
  .person-name .first { color: var(--orange); }
  .person-role { font-size: 14px; margin-bottom: 16px; }
  .contact-list { list-style: none; font-size: 12.5px; }
  .contact-list li {
    display: flex; align-items: center; gap: 8px;
    margin-bottom: 6px;
  }
  .contact-list svg { width: 13px; height: 13px; flex: none; }

  /* Back */
  .card-back .pattern {
    position: absolute; inset: 0;
    background: linear-gradient(135deg, var(--navy-deep) 0%, var(--navy) 45%, var(--pattern-blue) 100%);
  }
  .back-brand {
    position: absolute;
    right: 70px; bottom: 70px;
    display: flex; align-items: center; gap: 7px;
    font-size: 15px; font-weight: 600;
  }
  .back-brand .brand-dot { width: 9px; height: 9px; }
</style>
</head>
<body>
  <section class="card card-front">
    <div class="brand-block">
      <div class="brand-name"><span class="brand-dot"></span>Skylark Reelworks</div>
    </div>
    <p class="credentials">NRD Certified Remote Pilot<br>Fully Insured</p>
    <div class="divider"></div>
    <div class="contact-block">
      <h1 class="person-name"><span class="first">Owen</span> Tarrick</h1>
      <p class="person-role">Owner</p>
      <ul class="contact-list">
        <li>
          <svg viewBox="0 0 16 16" aria-hidden="true"><path fill="#ef8a3c" d="M3.6 1.5l2.2 2.6-1.3 1.7c.9 2 2.6 3.7 4.7 4.7l1.7-1.3 2.6 2.2-1.4 2.2C6.8 13.3 2.7 9.2 1.4 3z"/></svg>
          614-502-7738
        </li>
        <li>
          <svg viewBox="0 0 16 16" aria-hidden="true"><g fill="none" stroke="#ef8a3c" stroke-width="1.4"><circle cx="8" cy="8" r="6.3"/><ellipse cx="8" cy="8" rx="2.7" ry="6.3"/><path d="M1.7 8h12.6"/></g></svg>
          www.skylarkreelworks.example
        </li>
        <li>
          <svg viewBox="0 0 16 16" aria-hidden="true"><g fill="none" stroke="#ef8a3c" stroke-width="1.4"><rect x="1.5" y="3.5" width="13" height="9"/><path d="M1.5 3.5L8 9l6.5-5.5"/></g></svg>
          info@skylarkreelworks.example
        </li>
      </ul>
    </div>
  </section>

  <section class="card card-back">
    <div class="pattern" role="img" aria-label="Repeating pattern of small drone silhouettes in shades of blue"></div>
    <div class="back-brand"><span class="brand-dot"></span>Skylark Reelworks</div>
  </section>
</body>
</html>
```